Varentoria Business Card and Letter Head

We are a leadership assessment consultancy based in Sydney, Australia. We help executive-level decison-makers select leaders for more senior level roles in corporate and government organisations. Our methodology is based on the latest research from the field of neuroscience.
We need a business card design and matching letter head that presents our company, Varentoria, as a:
1. trusted adviser to senior executive-level decison makers
2. niche consultancy who are experts in the field of assessing leadership talent
3. results-focused solution provider who balance scientific methods with pragmatic solutions
The following company details should be used in all designs:
Company Name: Varentoria
Details (for business card):
Derek Hanford
Prime Capacity Officer
Level 14, Marlow Tower
7 Marlow Square
Sydney, NSW 2150 Australia
Phone: 1300 582 714
Mobile: 0412 637 258
Email: derek.hanford@varentoria-example.com.au
Website: varentoria-example.com.au
I have attached the logo for Varentoria (for both a white and black background) - your business card and letter head designs must incoporate this logo and colour scheme.
Thanks for your interest in this project, I'm looking forward to receiving your ideas.
Regards,
Derek
Target Market(s)
Executive-level decison-makers in corporate and government organisations (e.g., CEO, VP, Head of Human Resources)
Industry/Entity Type
Leadership
Look and feel

```html
<!DOCTYPE html>
<html lang="en">
<head>
<meta charset="utf-8">
<title>Varentoria Business Card</title>
<link rel="stylesheet" href="https://fonts.googleapis.com/css2?family=Source+Sans+3:wght@400;600;700&display=swap">
<style>
  :root {
    --brand-red: #bd2a1c;
    --ink: #3b3b3b;
    --ink-soft: #555555;
    --paper: #ffffff;
    --backdrop: #ecebe8;
    --rule: #b9b9b9;
  }
  * { box-sizing: border-box; margin: 0; padding: 0; }
  html, body { width: 1200px; height: 1094px; overflow: hidden; }
  body {
    background: var(--backdrop);
    font-family: "Source Sans 3", "Helvetica Neue", Arial, sans-serif;
    position: relative;
  }
  .card {
    position: absolute;
    width: 760px;
    height: 440px;
    border-radius: 34px;
    overflow: hidden;
    box-shadow: 0 6px 18px rgba(0,0,0,0.18);
  }
  /* Front */
  .card-front { left: 60px; top: 60px; background: var(--paper); }
  .brand-lockup { position: absolute; left: 56px; top: 210px; }
  .brand-row { display: flex; align-items: center; gap: 14px; }
  .brand-square { width: 46px; height: 46px; background: var(--brand-red); }
  .brand-name { font-size: 50px; font-weight: 700; color: var(--ink); letter-spacing: -0.5px; line-height: 1; }
  .brand-tagline { margin-top: 6px; margin-left: 60px; font-size: 13.5px; letter-spacing: 1.2px; color: var(--brand-red); text-transform: uppercase; white-space: nowrap; }
  .divider { position: absolute; left: 380px; top: 40px; width: 2px; height: 200px; background: linear-gradient(var(--paper), var(--rule) 30%, var(--rule) 70%, var(--paper)); }
  .contact-block { position: absolute; left: 410px; top: 38px; }
  .person-name { font-size: 27px; font-weight: 700; color: var(--brand-red); }
  .person-title { font-size: 17px; color: var(--ink); margin-top: 2px; }
  .contact-list { list-style: none; margin-top: 24px; }
  .contact-list li { display: flex; align-items: center; gap: 10px; font-size: 15.5px; color: var(--ink); line-height: 24px; white-space: nowrap; }
  .contact-list svg { width: 14px; height: 14px; flex: none; fill: var(--ink); }
  .contact-list svg.icon-web { fill: none; stroke: var(--ink); stroke-width: 1.4; }
  .band-main { position: absolute; left: 0; top: 300px; width: 100%; height: 48px; background: var(--brand-red); }
  .band-upper { position: absolute; left: 545px; top: 250px; width: 215px; height: 44px; background: var(--brand-red); }
  .band-badge { position: absolute; left: 600px; top: 232px; width: 82px; height: 82px; background: var(--paper); display: flex; align-items: center; justify-content: center; }
  .band-badge span { width: 40px; height: 40px; background: var(--brand-red); }
  .address { position: absolute; left: 0; right: 0; top: 376px; text-align: center; font-size: 18px; color: var(--ink-soft); white-space: nowrap; }
  /* Back */
  .card-back { left: 380px; top: 594px; background: var(--brand-red); color: var(--paper); }
  .back-lockup { position: absolute; left: 80px; top: 110px; }
  .back-lockup .brand-square { width: 92px; height: 92px; background: var(--paper); }
  .back-lockup .brand-row { gap: 22px; }
  .back-lockup .brand-name { font-size: 84px; color: var(--paper); }
  .back-lockup .brand-tagline { margin-left: 114px; font-size: 20px; letter-spacing: 1.8px; color: var(--paper); margin-top: 8px; }
  .back-url { position: absolute; left: 0; right: 0; top: 330px; text-align: center; font-size: 27px; letter-spacing: 2px; color: var(--paper); }
</style>
</head>
<body>
  <section class="card card-front" aria-label="Business card front">
    <div class="brand-lockup">
      <div class="brand-row"><span class="brand-square"></span><span class="brand-name">Varentoria</span></div>
      <p class="brand-tagline">Assessing Executive Potential</p>
    </div>
    <div class="divider"></div>
    <div class="contact-block">
      <h1 class="person-name">Derek Hanford</h1>
      <p class="person-title">Prime Capacity Officer</p>
      <ul class="contact-list">
        <li><svg viewBox="0 0 16 16" aria-hidden="true"><path d="M3 1l3 0 1 4-2 1c1 2 3 4 5 5l1-2 4 1 0 3c0 1-1 2-2 2C7 15 1 9 1 3c0-1 1-2 2-2z"/></svg>1300 582 714</li>
        <li><svg viewBox="0 0 16 16" aria-hidden="true"><path d="M4 0h8a1 1 0 0 1 1 1v14a1 1 0 0 1-1 1H4a1 1 0 0 1-1-1V1a1 1 0 0 1 1-1zm1 2v9h6V2zm3 10a1.2 1.2 0 1 0 0 2.4A1.2 1.2 0 0 0 8 12z"/></svg>0412 637 258</li>
        <li><svg viewBox="0 0 16 16" aria-hidden="true"><path d="M0 3h16v1L8 9 0 4zm0 3l8 5 8-5v7H0z"/></svg>derek.hanford@varentoria-example.com.au</li>
        <li><svg class="icon-web" viewBox="0 0 16 16" aria-hidden="true"><circle cx="8" cy="8" r="6.5"/><ellipse cx="8" cy="8" rx="3" ry="6.5"/><path d="M1.5 8h13"/></svg>varentoria-example.com.au</li>
      </ul>
    </div>
    <div class="band-upper"></div>
    <div class="band-main"></div>
    <div class="band-badge"><span></span></div>
    <p class="address">Level 14, Marlow Tower 7 Marlow Square Sydney, NSW 2150 Australia</p>
  </section>

  <section class="card card-back" aria-label="Business card back">
    <div class="back-lockup">
      <div class="brand-row"><span class="brand-square"></span><span class="brand-name">Varentoria</span></div>
      <p class="brand-tagline">Assessing Executive Potential</p>
    </div>
    <p class="back-url">www.varentoria-example.com.au</p>
  </section>
</body>
</html>
```